Dog Snacks brand needs a new packaging design

Dear Designers,

We are looking for a packaging expert to design our new line of Dog Snacks which contain a relaxing hemp extract (CBD).

Our company is already selling various relaxing cat & dog products , and we would like this new design to reflect the same "style & feeling" as our current products (see attached instructions).

Technical aspects:
- The packaging is a Stand Up Pouch (12x18.5x7cm - see attached instructions).
- Please follow technical guidelines from printer (see attached instructions).
- The packaging will contain 120g of high-quality, semi-moist dog snacks.
- We will be designing 3 differents variations for 3 different flavours: Chicken, Beef & Liver.
- The packaging will be printed with a matt finish.

Design aspects:
- The design should be compatible with our brand identity (i.e. fluffly, pure, relaxing, positive, clean & natural).
- Soft/rounded shapes are preferred.
- Please use our brand's colors (#3BA384, White & Black).
- Please use our company logo (see attached instructions).
- The design also needs to convey a strong sense of professionalism as we are an animal "healthcare" brand.
- If you want to include a dog picture, we would prefer you to use a picture of our official brand ambassador (see attached instructions).
- We have attached a number of packaging examples which we like a lot. (see attached instructions). Please only use those as general inspiration.
- Only original work (no plagiarism will be accepted).

Please don't hesitate to send us a message if you have any questions about the brand, the product or the design requirements.

We look forward to seeing your designs & working on this together !

Thanks & regards,
Tobias

Target Market(s)

Dog owners

Industry/Entity Type

Pet Care

Font styles to use
Sans Serif

Requirements
Must have
• Please see project description.
Nice to have
Should not have

```html
<!DOCTYPE html>
<html lang="en">
<head>
<meta charset="utf-8">
<title>VERDALIS For Animals – VerdaBites CBD Treats Pouch</title>
<link rel="stylesheet" href="https://fonts.googleapis.com/css2?family=Arvo:wght@400;700&family=Roboto+Slab:wght@400;500;700&display=swap">
<style>
  :root {
    --backdrop: #178a69;
    --brand: #1f8f6b;
    --brand-deep: #14785a;
    --brand-soft: #6cbfa2;
    --paper: #ffffff;
    --paper-shade: #eef1f0;
    --ink: #1b1b1b;
  }
  * { box-sizing: border-box; margin: 0; padding: 0; }
  html, body { width: 1200px; height: 818px; overflow: hidden; }
  body {
    background: var(--backdrop);
    font-family: "Roboto Slab", serif;
    position: relative;
  }
  .pouch {
    position: absolute;
    top: 108px;
    height: 576px;
    background: linear-gradient(180deg, var(--paper) 0%, var(--paper) 70%, var(--paper-shade) 100%);
    border-radius: 14px 14px 6px 6px;
    overflow: hidden;
  }
  .pouch--front { left: 300px; width: 330px; }
  .pouch--back { left: 694px; width: 332px; }
  .pouch__seam { position: absolute; left: 0; top: 0; width: 100%; height: 130px; }
  .pouch__paw-band {
    position: absolute; left: 0; bottom: 16px; width: 100%; height: 70px;
    background: linear-gradient(180deg, var(--brand) 0%, var(--brand-soft) 100%);
  }
  .abs { position: absolute; }
  .brand-mark {
    position: absolute; border-radius: 50%;
    border: 3px solid var(--brand); background: transparent;
  }
  .brand-name {
    position: absolute; font-family: "Arvo", serif; font-weight: 400;
    color: var(--ink); letter-spacing: 0.5px; white-space: nowrap;
    transform: translateX(-50%);
  }
  .brand-tagline {
    position: absolute; color: var(--brand); font-weight: 500; white-space: nowrap;
    transform: translateX(-100%);
  }
  .product-name {
    position: absolute; left: 46px; top: 262px;
    font-family: "Arvo", serif; font-weight: 700; font-size: 37px;
    color: var(--brand); letter-spacing: -0.5px; white-space: nowrap; line-height: 1;
  }
  .product-name sup { font-size: 13px; font-weight: 400; vertical-align: 20px; margin-left: 3px; }
  .rule { position: absolute; height: 1.5px; background: var(--brand); }
  .product-type {
    left: 46px; top: 334px; font-family: "Arvo", serif; font-weight: 700;
    font-size: 21px; line-height: 1; color: var(--brand); white-space: nowrap;
  }
  .benefits {
    left: 46px; top: 364px; font-size: 9px; font-weight: 700; line-height: 1;
    color: var(--brand); white-space: nowrap;
  }
  .thc {
    left: 46px; top: 388px; font-family: "Arvo", serif; font-weight: 700;
    font-size: 20px; line-height: 1; color: var(--brand);
  }
  .dog-figure {
    left: 210px; top: 340px; width: 66px; height: 76px;
    background: var(--brand-soft); border-radius: 16px 20px 6px 6px;
  }
  .facts {
    position: absolute; left: 40px; top: 434px; width: 256px; height: 36px;
    display: flex; align-items: center; gap: 7px;
    font-size: 10px; font-weight: 700; color: var(--brand); line-height: 1.1;
  }
  .facts__item { display: flex; align-items: center; gap: 4px; white-space: nowrap; }
  .facts__icon { width: 16px; height: 18px; background: var(--brand); border-radius: 3px; }
  .facts__divider { width: 1.5px; height: 28px; background: var(--brand-soft); }
  .facts__seal { width: 24px; height: 24px; border-radius: 50%; border: 1.5px solid var(--brand-soft); }
  .story-panel {
    position: absolute; left: 6px; top: 134px; width: 162px; height: 254px;
    background: var(--brand); border-radius: 0 18px 0 0;
    color: var(--paper); text-align: center; padding: 36px 10px 0 14px;
  }
  .story-panel__title { font-family: "Arvo", serif; font-size: 10.5px; line-height: 1.35; margin-bottom: 18px; }
  .story-panel p { font-size: 7px; line-height: 1.45; margin-bottom: 9px; }
  .info { position: absolute; left: 174px; width: 152px; text-align: center; color: var(--brand); }
  .info h3 { font-family: "Arvo", serif; font-weight: 700; font-size: 10.5px; color: var(--ink); margin-bottom: 2px; }
  .info p { font-size: 7px; line-height: 1.4; }
  .code-box { left: 42px; top: 428px; width: 88px; height: 52px; background: var(--brand); }
  .distributor { left: 150px; top: 428px; font-size: 7.5px; line-height: 1.3; color: var(--brand); }
  .distributor strong { display: block; font-size: 9.5px; color: var(--ink); font-weight: 500; }
  .vet-seal { left: 240px; top: 428px; width: 48px; height: 48px; border-radius: 50%; border: 2px solid var(--brand-soft); }
</style>
</head>
<body>

<section class="pouch pouch--front" aria-label="Pouch front">
  <svg class="pouch__seam" viewBox="0 0 330 130" preserveAspectRatio="none">
    <path d="M0 76 H134 Q158 80 165 116 Q172 80 196 76 H330" fill="none" stroke="var(--brand)" stroke-width="7"/>
  </svg>
  <span class="brand-mark" style="left:148px;top:146px;width:28px;height:28px;"></span>
  <span class="brand-name" style="left:165px;top:186px;font-size:34px;">VERDALIS</span>
  <span class="brand-tagline" style="left:249px;top:228px;font-size:12.5px;">For Animals</span>
  <h1 class="product-name">VerdaBites<sup>TM</sup></h1>
  <div class="rule" style="left:46px;top:328px;width:140px;"></div>
  <div class="abs product-type">CBD TREATS</div>
  <div class="abs benefits">▪ SUPPORT | ▪ CALM | ▪ EASE</div>
  <div class="abs thc">0% THC</div>
  <div class="abs dog-figure" role="img" aria-label="Silhouette of the brand's dog ambassador standing in profile"></div>
  <div class="rule" style="left:46px;top:420px;width:244px;background:var(--brand-soft);"></div>
  <div class="facts">
    <span class="facts__item"><span class="facts__icon"></span>Chicken</span>
    <span class="facts__divider"></span>
    <span class="facts__item"><span class="facts__icon"></span>120g</span>
    <span class="facts__divider"></span>
    <span class="facts__item"><span class="facts__icon"></span>CBD<br>250mg</span>
    <span class="facts__divider"></span>
    <span class="facts__seal"></span>
  </div>
  <div class="pouch__paw-band" role="img" aria-label="Band of repeating white paw prints"></div>
</section>

<section class="pouch pouch--back" aria-label="Pouch back">
  <svg class="pouch__seam" viewBox="0 0 332 130" preserveAspectRatio="none">
    <path d="M0 76 H184 Q204 80 210 116 Q216 80 236 76 H332" fill="none" stroke="var(--brand)" stroke-width="7"/>
  </svg>
  <div class="story-panel">
    <h2 class="story-panel__title">GIVE THEM THE TREAT<br>OF JOY:</h2>
    <p>Fear of abandonment, separation anxiety, phobias and behaviour problems can disturb your faithful companion's inner balance and peace of mind.</p>
    <p>VERDALIS has specially formulated these CBD-infused treats so that your dog can live a more relaxing life.</p>
    <p>These treats are rich in poultry and vegetables, plus they taste just as good as the natural feeling of well-being and joy they bring!</p>
  </div>
  <span class="brand-mark" style="left:228px;top:140px;width:22px;height:22px;border-width:2.5px;"></span>
  <span class="brand-name" style="left:250px;top:170px;font-size:23px;">VERDALIS</span>
  <span class="brand-tagline" style="left:304px;top:197px;font-size:10px;">For Animals</span>
  <div class="info" style="top:226px;">
    <h3>STORAGE &amp; WARNING:</h3>
    <p>Store at room temperature (15-25°C) in a cool, dry place away from light. Supplementary food exclusively for pets. If in doubt, consult your veterinarian.</p>
  </div>
  <div class="info" style="top:296px;">
    <h3>INGREDIENTS:</h3>
    <p>Meat and animal derivatives (20% poultry), cereals, derivatives of vegetable origin, hemp extract (0% THC). Analytical constituents: crude protein (31%), crude fat (5.5%), crude fibre (2%), crude ash (5%), moisture (25%).</p>
  </div>
  <div class="abs code-box"></div>
  <div class="abs distributor">
    <strong>Distributed by:</strong>
    VERDA EUROPE KFT.<br>Lomb utca 14<br>1071 Budapest<br>Hungary
  </div>
  <div class="abs vet-seal"></div>
  <div class="pouch__paw-band" role="img" aria-label="Band of repeating white paw prints"></div>
</section>

</body>
</html>
```